Verdant Systems Business Card

want the back of card to be blue- with the logo in the center
front of card- info plus logo (info being mailing address, email address, and website address )
4 different names with titles to have on cards
1) Calvin Borsted - Owner
2) Naomi Trelvik- Customer Relationship Specialist
3) Felix Andrade- Vice President of Sales
4) Owen Markby- Chief Technology Officer

Target Market(s)

tech company in the government/probation office industry

Industry/Entity Type

Government Office

Contact Information for Business Card

1) Calvin Borsted - Owner

Colors
0355a3
ffffff

Requirements
Must have
• back side should be blue, with the logo placed in the center
• front side needs to include both the logo, as well as company info (info should include website address, email address, and mailing address)

```html
<!DOCTYPE html>
<html lang="en">
<head>
<meta charset="utf-8">
<title>Verdant Systems Business Card</title>
<link href="https://fonts.googleapis.com/css2?family=Crimson+Pro:wght@600&family=Roboto:wght@400&display=swap" rel="stylesheet">
<style>
  :root {
    --blue: #0355a3;
    --grey: #7f8084;
    --text: #4a4a4d;
    --white: #ffffff;
    --backdrop: #e9e9eb;
    --circle-tint: #e3ecf6;
  }
  html, body {
    margin: 0;
    padding: 0;
    overflow: hidden;
  }
  .canvas {
    position: relative;
    width: 1125px;
    height: 1200px;
    background: var(--backdrop);
    overflow: hidden;
  }
  .card {
    position: absolute;
    left: 171px;
    width: 826px;
    height: 470px;
    box-shadow: 0 3px 8px rgba(0,0,0,0.25);
    overflow: hidden;
  }
  .card--front { top: 106px; background: var(--white); }
  .card--back { top: 639px; background: var(--blue); }

  .wordmark {
    position: absolute;
    left: 54px;
    top: 52px;
    margin: 0;
    font-family: "Crimson Pro", serif;
    font-weight: 600;
    font-size: 46px;
    line-height: 1;
    color: var(--blue);
  }
  .emblem {
    position: absolute;
    left: 420px;
    top: 36px;
    width: 390px;
    height: 390px;
    border-radius: 50%;
    background: var(--circle-tint);
  }
  .person {
    position: absolute;
    left: 54px;
    top: 222px;
  }
  .person__name {
    margin: 0;
    font-family: "Crimson Pro", serif;
    font-weight: 600;
    font-size: 33px;
    line-height: 1;
    color: var(--blue);
  }
  .person__title {
    margin: 4px 0 0;
    font-family: "Roboto", sans-serif;
    font-size: 20px;
    color: var(--grey);
  }
  .contact {
    position: absolute;
    left: 52px;
    top: 302px;
    margin: 0;
    padding: 0;
    list-style: none;
    font-family: "Roboto", sans-serif;
    font-size: 18px;
    color: var(--text);
  }
  .contact__item {
    display: flex;
    align-items: center;
    height: 26px;
    white-space: nowrap;
  }
  .contact__icon {
    flex: none;
    width: 18px;
    height: 18px;
    margin-right: 12px;
    fill: var(--blue);
  }

  .back-mark {
    position: absolute;
    left: 0;
    right: 0;
    top: 110px;
    text-align: center;
  }
  .back-mark__dot {
    display: block;
    width: 86px;
    height: 86px;
    margin: 0 auto 24px;
    border-radius: 50%;
    background: var(--white);
  }
  .back-mark__name {
    margin: 0;
    font-family: "Crimson Pro", serif;
    font-weight: 600;
    font-size: 58px;
    line-height: 1;
    color: var(--white);
  }
  .back-url {
    position: absolute;
    left: 0;
    right: 0;
    top: 392px;
    margin: 0;
    text-align: center;
    font-family: "Roboto", sans-serif;
    font-size: 19px;
    letter-spacing: 3px;
    color: var(--white);
  }
</style>
</head>
<body>
<div class="canvas">

  <section class="card card--front">
    <h1 class="wordmark">Verdant Systems</h1>
    <div class="emblem" aria-hidden="true"></div>

    <div class="person">
      <p class="person__name">Calvin Borsted</p>
      <p class="person__title">Owner</p>
    </div>

    <ul class="contact">
      <li class="contact__item">
        <svg class="contact__icon" viewBox="0 0 24 24"><path d="M6.6 10.8a15.1 15.1 0 0 0 6.6 6.6l2.2-2.2a1 1 0 0 1 1-.25 11.4 11.4 0 0 0 3.6.57 1 1 0 0 1 1 1V20a1 1 0 0 1-1 1A17 17 0 0 1 3 4a1 1 0 0 1 1-1h3.5a1 1 0 0 1 1 1c0 1.25.2 2.45.57 3.57a1 1 0 0 1-.25 1z"/></svg>
        555-214-7360
      </li>
      <li class="contact__item">
        <svg class="contact__icon" viewBox="0 0 24 24"><path d="M7 1h10a2 2 0 0 1 2 2v18a2 2 0 0 1-2 2H7a2 2 0 0 1-2-2V3a2 2 0 0 1 2-2zm0 3v14h10V4z"/></svg>
        555-308-4192
      </li>
      <li class="contact__item">
        <svg class="contact__icon" viewBox="0 0 24 24"><path d="M2 5h20v14H2zm2 2v.5l8 5 8-5V7l-8 5z"/></svg>
        hello@verdantsystems.com
      </li>
      <li class="contact__item">
        <svg class="contact__icon" viewBox="0 0 24 24"><path d="M12 2a10 10 0 1 0 0 20 10 10 0 0 0 0-20zm-1 17.9A8 8 0 0 1 4.1 11H7l2 2v2l2 2zm6.9-2.9A2 2 0 0 0 16 16h-1v-3a1 1 0 0 0-1-1H8v-2h2a1 1 0 0 0 1-1V7h2a2 2 0 0 0 2-2v-.4A8 8 0 0 1 17.9 17z"/></svg>
        www.verdantsystems.com
      </li>
      <li class="contact__item">
        <svg class="contact__icon" viewBox="0 0 24 24"><path d="M12 2a7 7 0 0 0-7 7c0 5.25 7 13 7 13s7-7.75 7-13a7 7 0 0 0-7-7zm0 9.5A2.5 2.5 0 1 1 12 6.5a2.5 2.5 0 0 1 0 5z"/></svg>
        1480 Harlow Ave, Suite 210, Ridgefield
      </li>
    </ul>
  </section>

  <section class="card card--back">
    <div class="back-mark">
      <span class="back-mark__dot" aria-hidden="true"></span>
      <p class="back-mark__name">Verdant Systems</p>
    </div>
    <p class="back-url">www.verdantsystems.com</p>
  </section>

</div>
</body>
</html>
```